Building Design company needing a letterhead

We need a letter head for our Building Design company to send letters etc. to our clients, consultants, councils etc. We would like to see our logo used and company colours. I have attached our style guide and an example of our current letterheads. Top left we would like our logo, top right we would like the company details and at the footer we would like some sort of image/design etc. that suits our brand. I like the Tarrow Design letterhead attached.

Target Market(s)

Professionals, Councils, Consultants, Mums & Dads

Industry/Entity Type

Architecture

Other font styles liked:
• refer the design style guide

Colors
f37122
000000
1b1b1b

Requirements
Must have
• Must have the minimum of a logo, company details and footer
Nice to have
• An image/design made for the footer that would suite our brand and website at www.corvanplans.com.au. Also it would be nice to include the KMEOT logo somewhere perhaps included in the footer.
Should not have
• Large images in the header. I just want the logo and company details.

```html
<!DOCTYPE html>
<html lang="en">
<head>
<meta charset="utf-8">
<title>Corvan Design Letterhead</title>
<link href="https://fonts.googleapis.com/css2?family=Titillium+Web:wght@700&family=Michroma&display=swap" rel="stylesheet">
<style>
  :root {
    --backdrop: #888888;
    --paper: #ffffff;
    --accent: #e95a24;
    --ink: #1b1b1b;
    --ghost: #f1f1f1;
  }
  * { margin: 0; padding: 0; box-sizing: border-box; }
  html, body {
    width: 847px; height: 1200px; overflow: hidden;
    background: var(--backdrop);
  }
  .sheet {
    position: absolute; left: 70px; top: 70px;
    width: 708px; height: 1059px;
    background: var(--paper);
    overflow: hidden;
  }
  .brand {
    position: absolute; left: 62px; top: 44px;
    display: flex; align-items: center; gap: 10px;
  }
  .brand-square { width: 30px; height: 40px; background: var(--accent); }
  .brand-name {
    font-family: "Titillium Web", sans-serif; font-weight: 700;
    font-size: 24px; line-height: 24px; letter-spacing: 1px;
    color: var(--ink); text-transform: uppercase;
  }
  .contact {
    position: absolute; right: 26px; top: 27px;
    text-align: right;
    font-family: "Michroma", sans-serif; color: var(--accent);
    text-transform: uppercase;
  }
  .contact .person { font-size: 9px; letter-spacing: 1.2px; line-height: 13px; }
  .contact .role { font-size: 7px; letter-spacing: 1px; line-height: 12px; margin-bottom: 5px; }
  .contact .line {
    display: flex; justify-content: flex-end; align-items: center; gap: 7px;
    font-size: 7px; letter-spacing: 1px; line-height: 17px;
  }
  .contact svg { width: 9px; height: 9px; fill: var(--accent); }
  .rule { position: absolute; left: 0; width: 100%; height: 6px; background: var(--accent); }
  .rule.top { top: 110px; }
  .rule.bottom { top: 989px; }
  .ghost-mark {
    position: absolute; left: 390px; top: 500px;
    transform: translate(-50%, -50%) rotate(-45deg);
    font-family: "Titillium Web", sans-serif; font-weight: 700;
    font-size: 68px; line-height: 70px; letter-spacing: 4px; color: var(--ghost);
    white-space: nowrap; text-transform: uppercase; text-align: left;
  }
  .address {
    position: absolute; left: 0; top: 1008px; width: 100%;
    text-align: center;
    font-family: "Michroma", sans-serif; color: var(--accent);
    font-size: 7px; letter-spacing: 1px; line-height: 17px;
    text-transform: uppercase;
  }
</style>
</head>
<body>
  <main class="sheet">
    <div class="brand">
      <span class="brand-square"></span>
      <div class="brand-name">Corvan<br>Design</div>
    </div>

    <div class="contact">
      <div class="person">Tomas Varley</div>
      <div class="role">Deisgnation</div>
      <div class="line">(123) 456-7890
        <svg viewBox="0 0 10 10"><path d="M2 0h2l1 3-1.5 1c.6 1.2 1.3 1.9 2.5 2.5L7 5l3 1v2c0 1-1 2-2 2C4 10 0 6 0 2 0 1 1 0 2 0z"/></svg>
      </div>
      <div class="line">info@companyname.com
        <svg viewBox="0 0 10 10"><path d="M0 2h10v6H0zM1 2.8v.4l4 2.6 4-2.6v-.4z"/></svg>
      </div>
      <div class="line">companyname.com
        <svg viewBox="0 0 10 10"><circle cx="5" cy="5" r="4.4" fill="none" stroke="#e95a24" stroke-width=".8"/><path d="M.6 5h8.8M5 .6v8.8" stroke="#e95a24" stroke-width=".6"/><ellipse cx="5" cy="5" rx="2" ry="4.4" fill="none" stroke="#e95a24" stroke-width=".6"/></svg>
      </div>
    </div>

    <div class="rule top"></div>

    <div class="ghost-mark" aria-hidden="true">Corvan<br>Design</div>

    <div class="rule bottom"></div>

    <div class="address">
      Address line1, address line2<br>
      Country - 123456
    </div>
  </main>
</body>
</html>
```